Brightmill Data Works

Our company is about IT hardwares and IT solutions. IT hardware such as PC, RAMS, storage and servers. IT solutions such as project management, BA. We are also selling new technology too.

Target Market(s)

Consumer, Small to Medium Business, Corporate

Requirements
Must have
• The business card must have the following:
• Name:
• Title:
• Contact Number:
• Email address:
• Website:
• Color: Must match the logo color upgrade

```html
<!DOCTYPE html>
<html lang="en">
<head>
<meta charset="utf-8">
<title>Brightmill Data Works – Business Card</title>
<link href="https://fonts.googleapis.com/css2?family=Lato:wght@400;700;900&display=swap" rel="stylesheet">
<style>
  :root {
    --page: #141414;
    --card-dark: #232323;
    --card-light: #ffffff;
    --amber: #e09a3a;
    --ink: #4a4a4a;
    --paper-text: #f2f2f2;
    --muted: #d8d8d8;
  }
  * { box-sizing: border-box; margin: 0; padding: 0; }
  html, body {
    width: 1200px; height: 912px; overflow: hidden;
    background: var(--page);
    font-family: "Lato", sans-serif;
  }
  .stage {
    width: 1200px; height: 912px;
    display: flex; flex-direction: column; align-items: center; justify-content: center;
    gap: 40px;
  }
  .card {
    position: relative;
    width: 700px; height: 400px;
    background: var(--card-dark);
    overflow: hidden;
    box-shadow: 0 10px 30px rgba(0,0,0,.5);
  }

  /* Front */
  .front-mark {
    position: absolute; left: 0; right: 0; top: 150px;
    display: flex; align-items: center; justify-content: center; gap: 16px;
  }
  .mark-dot {
    width: 26px; height: 26px; border-radius: 50%;
    background: var(--amber); flex: none;
  }
  .front-name {
    font-weight: 900; font-size: 40px; letter-spacing: 1px;
    color: var(--paper-text); text-transform: uppercase;
  }
  .front-web {
    position: absolute; left: 0; right: 0; bottom: 70px;
    text-align: center; color: var(--paper-text);
    font-size: 17px; letter-spacing: .5px;
  }

  /* Back */
  .back-shape { position: absolute; inset: 0; }
  .back-mark {
    position: absolute; left: 60px; top: 115px;
    display: flex; align-items: center; gap: 16px;
  }
  .back-name {
    font-weight: 900; font-size: 36px; line-height: 1.05; letter-spacing: .5px;
    color: var(--ink); text-transform: uppercase;
    width: 260px;
  }
  .address {
    position: absolute; left: 44px; bottom: 18px;
    color: var(--paper-text); font-size: 17px; line-height: 1.3;
  }
  .contact {
    position: absolute; right: 36px; top: 110px;
    text-align: right; color: var(--paper-text);
  }
  .person-name { color: var(--amber); font-size: 26px; font-weight: 700; }
  .person-title { font-size: 15px; margin: 2px 0 20px; color: var(--muted); }
  .contact-line {
    display: flex; align-items: center; justify-content: flex-end; gap: 10px;
    font-size: 15px; line-height: 25px;
  }
  .contact-line svg { width: 15px; height: 15px; flex: none; }
</style>
</head>
<body>
<main class="stage">

  <section class="card card-front" aria-label="Card front">
    <div class="front-mark">
      <span class="mark-dot"></span>
      <span class="front-name">Brightmill Data Works</span>
    </div>
    <p class="front-web">www.brightmilldata.com</p>
  </section>

  <section class="card card-back" aria-label="Card back">
    <svg class="back-shape" viewBox="0 0 700 400" width="700" height="400" aria-hidden="true">
      <path d="M0 0 H420 C490 80 470 220 330 280 C230 318 100 310 0 302 Z" fill="var(--card-light)"/>
      <path d="M440 0 C505 85 485 215 360 285" fill="none" stroke="var(--amber)" stroke-width="6" stroke-linecap="round"/>
    </svg>

    <div class="back-mark">
      <span class="mark-dot"></span>
      <span class="back-name">Brightmill Data Works</span>
    </div>

    <p class="address">418 Alder Row<br>Austin, TX 78704</p>

    <div class="contact">
      <p class="person-name">Daniel Ashford</p>
      <p class="person-title">Manager</p>
      <p class="contact-line">555 014 2200
        <svg viewBox="0 0 16 16" aria-hidden="true"><path d="M3 1.5l3 3-1.6 1.8a9 9 0 0 0 5.3 5.3L11.5 10l3 3-1.8 2C7 15 1 9 1 3.3z" fill="var(--amber)"/></svg>
      </p>
      <p class="contact-line">555 014 2201
        <svg viewBox="0 0 16 16" aria-hidden="true"><rect x="4" y="1" width="8" height="4" fill="var(--amber)"/><rect x="1" y="6" width="14" height="6" rx="1" fill="var(--amber)"/><rect x="4" y="10" width="8" height="5" fill="var(--card-dark)" stroke="var(--amber)" stroke-width="1.5"/></svg>
      </p>
      <p class="contact-line">info@brightmilldata.com
        <svg viewBox="0 0 16 16" aria-hidden="true"><rect x="1" y="3" width="14" height="10" fill="var(--amber)"/><path d="M1 3l7 6 7-6" fill="none" stroke="var(--card-dark)" stroke-width="1.5"/></svg>
      </p>
      <p class="contact-line">www.brightmilldata.com
        <svg viewBox="0 0 16 16" aria-hidden="true"><circle cx="8" cy="8" r="6.5" fill="none" stroke="var(--amber)" stroke-width="1.8"/><ellipse cx="8" cy="8" rx="2.8" ry="6.5" fill="none" stroke="var(--amber)" stroke-width="1.4"/><path d="M1.5 8h13" stroke="var(--amber)" stroke-width="1.4"/></svg>
      </p>
    </div>
  </section>

</main>
</body>
</html>
```